Need Business Card for our Real Estate Business with Sales Executive's Picture

PANTONE 484 C ( RED)

PANTONE 2766 C ( BLUE

Industry/Entity Type

Real Estate

Contact Information for Business Card

Name, Mobile, email, & picture of Person
Agency Phone, address, Web address

Requirements
Must have
• Our Logo Colours, Agent Picture,

```html
<!DOCTYPE html>
<html lang="en">
<head>
<meta charset="utf-8">
<title>Mesa Ridge Realty – Business Card</title>
<link href="https://fonts.googleapis.com/css2?family=Open+Sans:ital,wght@0,400;0,600;0,700;1,700&display=swap" rel="stylesheet">
<style>
  :root {
    --navy: #1b2a5c;
    --red: #a3262a;
    --white: #ffffff;
    --paper: #f7f7f8;
    --backdrop: #d9d9db;
    --ink: #1b2a5c;
  }
  * { box-sizing: border-box; margin: 0; padding: 0; }
  html, body { width: 1200px; height: 852px; overflow: hidden; }
  body {
    background: var(--backdrop);
    font-family: "Open Sans", Arial, sans-serif;
    position: relative;
  }
  .card {
    position: absolute;
    width: 520px;
    height: 300px;
    border-radius: 22px;
    overflow: hidden;
    box-shadow: 0 4px 14px rgba(0,0,0,0.18);
  }

  /* Back side */
  .card-back {
    left: 70px; top: 276px;
    background: var(--navy);
    color: var(--white);
  }
  .card-back .brand {
    position: absolute;
    left: 0; right: 0; top: 110px;
    text-align: center;
    font-weight: 600;
    font-size: 38px;
    letter-spacing: 3px;
    line-height: 52px;
  }
  .card-back .brand-rule {
    position: absolute;
    left: 130px; width: 260px; top: 170px;
    height: 1px; background: var(--white);
    opacity: 0.8;
  }
  .card-back .web {
    position: absolute;
    left: 0; right: 0; top: 188px;
    text-align: center;
    font-size: 13px;
    letter-spacing: 0.5px;
  }
  .card-back .accent {
    position: absolute;
    height: 3px; width: 70px;
    background: var(--red);
    top: 196px;
  }
  .card-back .accent.left { left: 70px; }
  .card-back .accent.right { right: 70px; }

  /* Front side */
  .card-front {
    left: 610px; top: 276px;
    background: var(--paper);
  }
  .card-front .waves { position: absolute; inset: 0; }
  .card-front .person {
    position: absolute;
    right: 22px; top: 12px;
    text-align: right;
    color: var(--white);
  }
  .card-front .person-name { font-weight: 700; font-style: italic; font-size: 16px; line-height: 20px; }
  .card-front .person-title { font-size: 11px; line-height: 14px; }
  .card-front .portrait {
    position: absolute;
    right: 0; top: 100px;
    width: 150px; height: 200px;
    background: linear-gradient(180deg, #e9e3df 0%, #c9a48c 38%, #2e4a8e 62%, #1f3570 100%);
  }
  .card-front .brand {
    position: absolute;
    left: 40px; top: 170px;
    display: flex; align-items: center; gap: 10px;
    color: var(--ink);
    font-weight: 600;
    font-size: 20px;
    line-height: 26px;
    letter-spacing: 2px;
  }
  .card-front .brand-mark {
    width: 11px; height: 11px; background: var(--red);
  }
  .card-front .contact {
    position: absolute;
    left: 40px; top: 204px;
    list-style: none;
    color: var(--ink);
    font-size: 12px;
    line-height: 16px;
  }
  .card-front .contact li { display: flex; align-items: center; gap: 8px; }
  .card-front .contact svg { width: 11px; height: 11px; flex: none; }
</style>
</head>
<body>

<section class="card card-back" aria-label="Business card, back">
  <div class="brand">MESA RIDGE REALTY</div>
  <div class="brand-rule"></div>
  <span class="accent left"></span>
  <div class="web">www.mesaridgerealty.com</div>
  <span class="accent right"></span>
</section>

<section class="card card-front" aria-label="Business card, front">
  <svg class="waves" viewBox="0 0 520 300" aria-hidden="true">
    <path d="M0,0 H520 V64 C410,70 300,84 200,104 C120,120 50,128 0,138 Z" fill="var(--navy)"/>
    <path d="M520,64 C410,70 300,84 200,104 C120,120 50,128 0,138" transform="translate(0 9)" fill="none" stroke="var(--red)" stroke-width="6"/>
    <path d="M520,64 C410,70 300,84 200,104 C120,120 50,128 0,138" transform="translate(0 21)" fill="none" stroke="var(--red)" stroke-width="4"/>
  </svg>

  <div class="person">
    <div class="person-name">Dana Whitfield</div>
    <div class="person-title">Managing Director</div>
  </div>

  <div class="portrait" role="img" aria-label="Portrait photo of Dana Whitfield in a navy suit"></div>

  <div class="brand"><span class="brand-mark"></span>MESA RIDGE REALTY</div>

  <ul class="contact">
    <li>
      <svg viewBox="0 0 12 12"><path d="M2.5 1 L4.5 1 L5.2 3.4 L4 4.4 C4.6 6 6 7.4 7.6 8 L8.6 6.8 L11 7.5 L11 9.5 C11 10.3 10.3 11 9.5 11 C5 11 1 7 1 2.5 C1 1.7 1.7 1 2.5 1 Z" fill="var(--red)"/></svg>
      303.555.0147
    </li>
    <li>
      <svg viewBox="0 0 12 12"><rect x="3" y="0.5" width="6" height="11" rx="1.2" fill="var(--red)"/><rect x="4" y="2" width="4" height="7" fill="var(--paper)"/></svg>
      720-555-0192
    </li>
    <li>
      <svg viewBox="0 0 12 12"><circle cx="6" cy="6" r="5" fill="none" stroke="var(--red)" stroke-width="1.3"/><path d="M1 6 H11 M6 1 C3.5 4 3.5 8 6 11 M6 1 C8.5 4 8.5 8 6 11" fill="none" stroke="var(--red)" stroke-width="1"/></svg>
      mesaridgerealty.com
    </li>
    <li>
      <svg viewBox="0 0 12 12"><rect x="0.5" y="2" width="11" height="8" fill="var(--red)"/><path d="M0.5 2 L6 6.5 L11.5 2" fill="none" stroke="var(--paper)" stroke-width="1"/></svg>
      dwhitfield@mesaridgerealty.com
    </li>
    <li>
      <svg viewBox="0 0 12 12"><path d="M6 0.5 C3.8 0.5 2.2 2.1 2.2 4.2 C2.2 7 6 11.5 6 11.5 C6 11.5 9.8 7 9.8 4.2 C9.8 2.1 8.2 0.5 6 0.5 Z" fill="var(--red)"/><circle cx="6" cy="4.2" r="1.4" fill="var(--paper)"/></svg>
      418 Alder Ave #210, Lakewood, CO 80226
    </li>
  </ul>
</section>

</body>
</html>
```